High-end construction company needs a business card design

We need a modern looking business card that draws people in, is memorable and looks so good people will want to sick it on their fridges.
On the first side what is needed are:
Logo
My name - Tomasz Brelwik
Title - Managing Director
Website - www.varkelt.co.uk
Email - tomasz@varkelt.co.uk
Telephone - 020 5194 6281
Mobile - 07845139072
On the back side was is needed is a list of all the services we provide:
-Kitchen Renovations
-Bathroom Renovations
-House Renovations
-Garage Conversions
-Extensions
-Loft Conversions
-Conservatories
-Carpentry
-Tiling
-Electrical
-Plumbing & Heating
-Bricklaying
-Landscaping
-Decorating
-Plastering
We would like the colours to be the same shades as on the logo with grey or black for the words.
Target Market(s)
Anyone who needs building work done
Contact Information for Business Card
This business card is for a construction company which strives to deliver excellent service and quality.
The look and feel of the card should represent this.
Requirements
Must have
- On the first side what is needed are:
Logo
My name - Tomasz Brelwik
Title - Managing Director
Website - www.varkelt.co.uk
Email - tomasz@varkelt.co.uk
Telephone - 020 5194 6281
Mobile - 07845139072
Nice to have
- Cool looking features

```html
<!DOCTYPE html>
<html lang="en">
<head>
<meta charset="UTF-8">
<title>Varkelt Construction Ltd – Business Card</title>
<link href="https://fonts.googleapis.com/css2?family=Montserrat:wght@400;500;700;800&display=swap" rel="stylesheet">
<style>
  :root{
    --green-light:#6cc24a;
    --green:#4fae36;
    --green-dark:#2f8a2a;
    --text-grey:#555a5e;
    --paper:#ffffff;
    --backdrop:#e9ebec;
  }
  *{box-sizing:border-box;margin:0;padding:0}
  html,body{width:1200px;height:965px;overflow:hidden;background:var(--backdrop);font-family:'Montserrat',sans-serif}
  .canvas{position:relative;width:1200px;height:965px}

  .card{position:absolute;width:660px;height:380px;overflow:hidden;box-shadow:0 6px 18px rgba(0,0,0,.18)}

  /* back side: services */
  .card-back{left:70px;top:55px;background:radial-gradient(circle at 60% 25%,var(--green-light) 0%,var(--green) 45%,var(--green-dark) 100%)}
  .back-logo{position:absolute;left:0;right:0;top:52px;text-align:center;color:var(--paper)}
  .back-logo .wordmark{display:inline-flex;align-items:center;gap:12px;font-weight:800;font-size:64px;letter-spacing:2px;line-height:1}
  .back-logo .mark-square{width:18px;height:18px;background:var(--paper)}
  .back-logo .tagline{margin-top:8px;font-weight:800;font-size:17px;letter-spacing:5px}
  .services{position:absolute;left:0;right:0;top:196px}
  .service-band{height:30px;background:var(--paper);margin-bottom:10px;display:flex;align-items:center;justify-content:center;
    font-size:13px;font-weight:500;color:var(--text-grey);letter-spacing:.3px;white-space:nowrap}
  .service-band:nth-child(1){margin-left:56px;margin-right:0}
  .service-band:nth-child(2){margin-left:28px;margin-right:0}
  .service-band:nth-child(3){margin-left:78px;margin-right:0}
  .service-band:nth-child(4){margin-left:78px;margin-right:0}
  .dot{display:inline-block;width:9px;height:9px;border-radius:50%;background:var(--green);margin:0 7px}

  /* front side: contact */
  .card-front{left:470px;top:520px;background:var(--paper)}
  .front-logo{position:absolute;left:40px;top:130px;width:270px;text-align:center;color:var(--green)}
  .front-logo .wordmark{display:inline-flex;align-items:center;gap:9px;font-weight:800;font-size:48px;letter-spacing:1px;line-height:1}
  .front-logo .mark-square{width:14px;height:14px;background:var(--green)}
  .front-logo .tagline{margin-top:8px;font-weight:800;font-size:13px;letter-spacing:4px}
  .divider{position:absolute;left:328px;top:70px;width:2px;height:190px;background:var(--green)}
  .contact{position:absolute;left:352px;top:68px}
  .contact .name{font-weight:700;font-size:22px;color:var(--green);letter-spacing:1px;text-transform:uppercase}
  .contact .role{font-size:15px;color:var(--text-grey);margin-top:2px}
  .contact-list{list-style:none;margin-top:18px}
  .contact-list li{display:flex;align-items:center;gap:12px;font-size:15px;color:var(--text-grey);height:27px}
  .contact-list svg{width:17px;height:17px;flex:none}
  .contact-list .site strong{color:var(--green);font-weight:700}
  .band-light{position:absolute;left:250px;bottom:0;width:300px;height:20px;background:var(--green)}
  .band-dark{position:absolute;left:556px;bottom:0;width:104px;height:10px;background:var(--green-dark)}
  .band-base{position:absolute;left:0;bottom:0;width:250px;height:4px;background:var(--green-dark)}
</style>
</head>
<body>
<main class="canvas">

  <section class="card card-back" aria-label="Services side">
    <div class="back-logo">
      <div class="wordmark"><span class="mark-square"></span>VARKELT</div>
      <div class="tagline">CONSTRUCTION LTD</div>
    </div>
    <div class="services">
      <div class="service-band">KITCHEN RENOVATIONS<span class="dot"></span>BATHROOM RENOVATIONS<span class="dot"></span>HOUSE RENOVATIONS</div>
      <div class="service-band">GARAGE CONVERSIONS<span class="dot"></span>EXTENSIONS<span class="dot"></span>LOFT CONVERSIONS<span class="dot"></span>CONSERVATORIES</div>
      <div class="service-band">CARPENTRY<span class="dot"></span>TILING<span class="dot"></span>ELECTRICAL<span class="dot"></span>PLUMBING &amp; HEATING</div>
      <div class="service-band">BRICKLAYING<span class="dot"></span>LANDSCAPING<span class="dot"></span>DECORATING<span class="dot"></span>PLASTERING</div>
    </div>
  </section>

  <section class="card card-front" aria-label="Contact side">
    <div class="front-logo">
      <div class="wordmark"><span class="mark-square"></span>VARKELT</div>
      <div class="tagline">CONSTRUCTION LTD</div>
    </div>
    <div class="divider"></div>
    <div class="contact">
      <div class="name">Tomasz Brelwik</div>
      <div class="role">Managing Director</div>
      <ul class="contact-list">
        <li>
          <svg viewBox="0 0 24 24" fill="none" stroke="#4fae36" stroke-width="2"><rect x="7" y="2" width="10" height="20" rx="2"/><line x1="11" y1="18" x2="13" y2="18"/></svg>
          07845139072
        </li>
        <li>
          <svg viewBox="0 0 24 24" fill="none" stroke="#4fae36" stroke-width="2"><path d="M5 3h4l2 5-3 2a12 12 0 0 0 6 6l2-3 5 2v4a2 2 0 0 1-2 2A17 17 0 0 1 3 5a2 2 0 0 1 2-2z"/></svg>
          020 5194 6281
        </li>
        <li>
          <svg viewBox="0 0 24 24" fill="none" stroke="#4fae36" stroke-width="2"><rect x="3" y="5" width="18" height="14"/><polyline points="3,5 12,13 21,5"/></svg>
          tomasz@varkelt.co.uk
        </li>
        <li class="site">
          <svg viewBox="0 0 24 24" fill="none" stroke="#4fae36" stroke-width="2"><circle cx="12" cy="12" r="9"/><line x1="3" y1="12" x2="21" y2="12"/><ellipse cx="12" cy="12" rx="4" ry="9"/></svg>
          <span>www.<strong>varkelt</strong>.co.uk</span>
        </li>
      </ul>
    </div>
    <div class="band-base"></div>
    <div class="band-light"></div>
    <div class="band-dark"></div>
  </section>

</main>
</body>
</html>
```